Coastline Premier Retreats Business Card Design

Design a business card for Coastline Premier Retreats. Look at the website for colors and reference. Card should have logo, name, title, office number, mobile number, email, URL and a tagline like, "Luxury Hotel & Resort Email Marketing" (This might change).

https://www.coastlinepremierretreats.example

The rest I will leave up to your imagination.

Contact Information for Business Card

Logo, name, title, office number, mobile number, email, URL and a tagline like, "Luxury Hotel & Resort Email Marketing" (This might change).

```html
<!DOCTYPE html>
<html lang="en">
<head>
<meta charset="UTF-8">
<title>Coastline Premier Retreats – Business Card</title>
<link href="https://fonts.googleapis.com/css2?family=Poppins:wght@300;400;600;700&display=swap" rel="stylesheet">
<style>
  :root {
    --stage: #1d1d1d;
    --orange: #f47f1f;
    --ink: #1f1f1f;
    --paper: #ffffff;
  }
  * { box-sizing: border-box; margin: 0; padding: 0; }
  html, body {
    width: 1200px; height: 1015px; overflow: hidden;
    background: var(--stage);
    font-family: "Poppins", sans-serif;
  }
  .sheet {
    position: relative; width: 1200px; height: 1015px;
  }
  .card {
    position: absolute; left: 290px; width: 620px; height: 354px;
    overflow: hidden;
  }
  .card--front { top: 100px; background: var(--orange); color: var(--paper); }
  .card--back { top: 540px; background: var(--paper); color: var(--ink); }

  .brand {
    display: flex; align-items: center; gap: 12px;
    font-weight: 700; font-size: 30px; letter-spacing: 1px;
    text-transform: uppercase; line-height: 1;
  }
  .brand__mark { width: 16px; height: 16px; background: currentColor; flex: none; }

  .card--front .brand { position: absolute; top: 132px; left: 0; right: 0; justify-content: center; }
  .tagline {
    position: absolute; bottom: 42px; left: 0; right: 0; text-align: center;
    font-weight: 700; font-size: 15px; letter-spacing: 1.5px; text-transform: uppercase;
  }

  .card--back .brand { position: absolute; top: 62px; left: 0; right: 0; justify-content: center; color: var(--ink); }
  .card--back .brand__mark { background: var(--orange); }

  .contact-band {
    position: absolute; top: 160px; left: 0; right: 0; height: 118px;
    background: var(--orange); color: var(--paper);
    display: flex; align-items: center; justify-content: center; gap: 28px;
  }
  .person { text-align: right; }
  .person__name { font-weight: 700; font-size: 22px; text-transform: uppercase; letter-spacing: .5px; line-height: 1.1; }
  .person__role { font-weight: 300; font-size: 16px; }
  .divider { width: 1px; height: 74px; background: var(--paper); }
  .contacts { list-style: none; font-size: 15px; font-weight: 400; line-height: 1.6; }
  .contacts li { display: flex; align-items: center; gap: 8px; }
  .contacts svg { width: 14px; height: 14px; fill: none; stroke: var(--paper); stroke-width: 2; flex: none; }

  .website {
    position: absolute; bottom: 26px; left: 0; right: 0; text-align: center;
    font-size: 16px; letter-spacing: 1.5px; color: var(--ink);
  }
</style>
</head>
<body>
<main class="sheet">
  <section class="card card--front">
    <div class="brand"><span class="brand__mark"></span>Coastline Premier Retreats</div>
    <p class="tagline">Luxury Hotel &amp; Resort Email Marketing</p>
  </section>

  <section class="card card--back">
    <div class="brand"><span class="brand__mark"></span>Coastline Premier Retreats</div>
    <div class="contact-band">
      <div class="person">
        <p class="person__name">Daniel Hartley</p>
        <p class="person__role">Managing Director</p>
      </div>
      <span class="divider"></span>
      <ul class="contacts">
        <li><svg viewBox="0 0 24 24"><path d="M5 3h4l2 5-3 2a12 12 0 0 0 6 6l2-3 5 2v4a2 2 0 0 1-2 2A17 17 0 0 1 3 5a2 2 0 0 1 2-2z"/></svg>044-555 010 220</li>
        <li><svg viewBox="0 0 24 24"><rect x="6" y="2" width="12" height="20" rx="2"/><path d="M11 18h2"/></svg>044-555 010 221</li>
        <li><svg viewBox="0 0 24 24"><rect x="3" y="5" width="18" height="14"/><path d="M3 5l9 8 9-8"/></svg>info@coastlinemail.example</li>
      </ul>
    </div>
    <p class="website">www.coastlinepremierretreats.example</p>
  </section>
</main>
</body>
</html>
```